Recruitment Site Design

We need a design for the login page, about page, and inner pages of a recruitment site for an oil and gas company. Design should be modern, sleek, professional and colors can be blue, green, white, orange or any other recommended colors.

Please also take into consideration that once the users login, they will need to access a form to fill in their information.

** UPDATE: Kindly provide a design for the inner information page consistent with the outer design. Attached is a picture of the basic structure. ***
Updates

Please provide a design for inner pages as shown in the design brief consistent with the registration page provided. 

Reason: We're extending it to get more inside pages.

Target Market(s)

Professionals looking for a career in the oil and gas industry in the Middle East.

Industry/Entity Type

Oil And Gas

Requirements
Must have
• Sleek design

```html
<!DOCTYPE html>
<html lang="en">
<head>
<meta charset="utf-8">
<title>Rigline – Jobs in Oil &amp; Gas</title>
<link href="https://fonts.googleapis.com/css2?family=Open+Sans:ital,wght@0,400;0,600;1,400&family=Roboto+Condensed:wght@400;700&display=swap" rel="stylesheet">
<style>
:root{
  --orange:#f47a10;
  --orange-light:#ff8a1e;
  --orange-deep:#c24a05;
  --dusk:#3a1a08;
  --ink:#222;
  --text:#555;
  --muted:#777;
  --rule:#dcdcdc;
  --dark-btn:#444;
  --page:#ececec;
  --white:#fff;
}
*{margin:0;padding:0;box-sizing:border-box}
html,body{width:854px;height:1200px;overflow:hidden}
body{position:relative;background:linear-gradient(#f4f4f4,var(--page));font-family:"Open Sans",sans-serif;color:var(--text)}
.abs{position:absolute}
.cond{font-family:"Roboto Condensed",sans-serif}

.site-header{left:0;top:0;width:854px;height:90px;border-top:2px solid #333;
  background:repeating-linear-gradient(135deg,#fafafa 0 3px,#f0f0f0 3px 4px)}
.brand{left:38px;top:30px;font-family:"Roboto Condensed",sans-serif;font-weight:700;font-size:38px;color:var(--ink);letter-spacing:.5px}
.main-nav{right:46px;top:55px;display:flex;gap:12px;font-family:"Roboto Condensed",sans-serif;font-size:12.5px;color:var(--ink)}
.main-nav .sep{color:#999}

.hero{left:0;top:90px;width:854px;height:308px;background:linear-gradient(90deg,var(--orange-light),var(--orange))}
.hero-photo{left:340px;top:90px;width:514px;height:332px;
  background:linear-gradient(180deg,#f58a1a 0%,#f07010 55%,#b84508 80%,var(--dusk) 100%)}
.hero-title{left:50px;top:150px;font-family:"Roboto Condensed",sans-serif;font-weight:700;font-size:35px;color:var(--white);letter-spacing:-.5px}
.hero-sub{left:50px;top:193px;font-family:"Roboto Condensed",sans-serif;font-weight:700;font-size:20px;color:var(--white)}
.hero-text{left:50px;top:230px;width:400px;font-size:9.5px;line-height:15px;color:#fff3e6}
.search{left:48px;top:272px;width:277px;height:32px;background:var(--white);border-radius:3px;display:flex;align-items:center}
.search span{flex:1;padding-left:14px;font-style:italic;font-size:10.5px;color:#aaa}
.search .go{width:32px;height:100%;border-left:1px solid #ddd;display:flex;align-items:center;justify-content:center}

.panel{left:37px;top:386px;width:781px;height:814px;background:var(--white);border-top:3px solid #ddd}
.intro{left:37px;top:389px;width:781px;height:86px;background:linear-gradient(#fff,#f2f2f2);
  display:flex;align-items:center;justify-content:center;text-align:center;padding:0 50px;
  font-family:"Roboto Condensed",sans-serif;font-weight:700;font-size:15.5px;line-height:19px;color:var(--ink)}

.section-title{font-family:"Roboto Condensed",sans-serif;font-weight:700;font-size:15px;color:var(--ink);
  padding-bottom:8px;border-bottom:1px solid var(--rule)}
.about{left:57px;top:499px;width:340px}
.about .lead{margin-top:10px;font-size:9px;font-weight:600;color:#333}
.about p{font-size:8.6px;line-height:15.3px;margin-top:7px}
.testimonials{left:57px;top:710px;width:340px}
.quote{position:absolute;left:2px;width:340px}
.quote .face{position:absolute;left:0;top:0;width:74px;height:71px;background:linear-gradient(#c9a890,#8a6a58);border-radius:2px}
.quote .body{position:absolute;left:88px;top:0;width:252px;font-size:8.6px;line-height:15.3px;font-style:italic}
.quote .body strong{display:block;font-weight:400;color:#333;margin-bottom:2px}
.quote .by{font-style:normal;font-weight:600;color:#333;margin-top:4px}
.view-all{font-family:"Roboto Condensed",sans-serif;font-weight:700;font-size:8.5px;color:#333}

.jobs{left:449px;top:499px;width:350px}
.job{position:absolute;left:-4px;width:354px;height:100px}
.job .thumb{position:absolute;left:0;top:0;width:88px;height:81px;background:linear-gradient(135deg,#7c8fa6,#2f4560 60%,#e07820);border-radius:2px}
.job .info{position:absolute;left:101px;top:0;width:254px}
.job h3{font-family:"Roboto Condensed",sans-serif;font-weight:700;font-size:12px;color:#333}
.job h3 small{font-weight:400;font-size:9.5px;margin-left:4px}
.job .loc{font-family:"Roboto Condensed",sans-serif;font-size:10px;color:#444;margin-top:5px}
.job p{font-size:8.3px;line-height:13.5px;margin-top:4px}
.btns{display:flex;gap:4px;margin-top:6px}
.btn{width:48px;height:17px;border-radius:2px;font-family:"Roboto Condensed",sans-serif;font-size:9px;color:#fff;display:flex;align-items:center;justify-content:center}
.btn.details{background:var(--dark-btn)}
.btn.apply{background:var(--orange)}

.sponsors-title{left:56px;top:1016px;width:742px;display:flex;align-items:center;gap:12px;
  font-family:"Roboto Condensed",sans-serif;font-weight:700;font-size:15px;color:var(--ink)}
.sponsors-title::before,.sponsors-title::after{content:"";flex:1;height:1px;background:var(--rule)}
.sponsors{left:70px;top:1048px;width:730px;height:42px;display:flex;justify-content:space-between;align-items:center;
  font-family:"Roboto Condensed",sans-serif;font-weight:700;font-size:13px;color:#888}
.sponsors span{display:flex;align-items:center;gap:5px}
.sponsors i{display:inline-block;width:14px;height:14px;background:#999;border-radius:50%}

.footer-rule{left:56px;top:1118px;width:743px;height:3px;background:#dcdcdc}
.footer-nav{left:61px;top:1137px;display:flex;gap:15px;font-size:9px;color:#333}
.copyright{left:61px;top:1162px;font-size:7.5px;color:#444}
.social{left:716px;top:1135px;display:flex;gap:7px}
.social i{width:16px;height:16px;border-radius:50%;background:#444;display:block}
</style>
</head>
<body>
<header class="abs site-header">
  <div class="abs brand">Rigline</div>
  <nav class="abs main-nav">
    <span>About Us</span><span class="sep">/</span><span>Jobs</span><span class="sep">/</span><span>Blog</span><span class="sep">/</span><span>Find Now</span><span class="sep">/</span><span>Location</span><span class="sep">/</span><span>Contact</span>
  </nav>
</header>

<section class="abs hero"></section>
<div class="abs hero-photo" role="img" aria-label="Oil drilling rig silhouetted against an orange sunset sky"></div>
<h1 class="abs hero-title">Jobs in Oil &amp; Gas Industry</h1>
<h2 class="abs hero-sub">Apply Now For Middle East Jobs</h2>
<p class="abs hero-text">Pellentesque habitant morbi tristique senectus et netus et malesuada fames ac turpis egestas. In posuere felis nec tortor. Pellentesque faucibus.</p>
<div class="abs search"><span>type your job for search</span><div class="go">
  <svg width="15" height="10" viewBox="0 0 15 10"><path d="M0 5h12M8 1l4 4-4 4" fill="none" stroke="#999" stroke-width="1.6"/></svg></div></div>

<main class="abs panel"></main>
<div class="abs intro">Pellentesque habitant morbi tristique senectus et netus et malesuada fames ac turpis egestas. In posuere felis nec tortor. Pellentesque faucibus. Ut accumsan ultricies elit.</div>

<section class="abs about">
  <h2 class="section-title">Little About Our Company</h2>
  <p class="lead">Lorem ipsum dolor sit amet, consectetuer adipiscing elit.</p>
  <p>Nam cursus. Morbi ut mi. Nullam enim leo, egestas id, condimentum at, laoreet mattis, massa. Sed eleifend nonummy diam. Praesent mauris ante, elementum et, bibendum at, posuere sit amet, nibh. Duis tincidunt lectus quis dui viverra vestibulum.</p>
  <p>Curabitur tristique mi condimentum orci. Phasellus pellentesque aliquam enim. Proin dui lectus, cursus eu, mattis laoreet, viverra sit amet, quam. Curabitur vel dolor ultrices ipsum dictum tristique. Praesent vitae lacus. Ut velit enim, vestibulum non, fermentum nec, hendrerit quis, leo. Pellentesque rutrum malesuada neque.</p>
</section>

<section class="abs testimonials">
  <h2 class="section-title">Testimonials</h2>
  <div class="quote" style="top:37px">
    <div class="face" role="img" aria-label="Portrait photo of a smiling client"></div>
    <div class="body"><strong>Pellentesque nibh libero, ultricies eu</strong>Nam cursus. Morbi ut mi.a Nullam enim leo, egestas id, condimentum at, laoreet mattis, massa. Sed eleifend nonummy diam. Praesent mauris ante, elementum et,<div class="by">By Author Name</div></div>
  </div>
  <div class="quote" style="top:142px">
    <div class="face" role="img" aria-label="Portrait photo of a smiling professional"></div>
    <div class="body"><strong>Pellentesque nibh libero, ultricies eu</strong>Maecenas aliquet velit vel turpis. Mauris neque metus, malesuada nec, ultricies sit amet, porttitor mattis, enim. In massa libero, interdum nec, interdum vel, blandit sed, nulla. In ullamcorper, est eget tempor cursus, neque mi consectetuer mi, a ultricies massa est sed nisl. Class aptent taciti sociosqu ad litora torquent.<div class="by">By Author Name</div></div>
  </div>
  <div class="view-all" style="position:absolute;left:305px;top:256px">VIEW ALL ▸</div>
</section>

<section class="abs jobs">
  <h2 class="section-title">Recent Jobs</h2>
  <article class="job" style="top:35px"><div class="thumb" role="img" aria-label="Engineer in orange overalls at a plant"></div>
    <div class="info"><h3>Name Job Tittle here &nbsp;|<small>Oil &amp; Gas Industry Company</small></h3><div class="loc">Location: Place of Middle East here</div>
    <p>Ut ante enim, dapibus malesuada, fringilla eu, condimentum quis, tellus. Aenean porttitor eros vel dolor. venenatis nibh.</p>
    <div class="btns"><span class="btn details">Details</span><span class="btn apply">Apply</span></div></div></article>
  <article class="job" style="top:146px"><div class="thumb" role="img" aria-label="Worker in hard hat using a radio"></div>
    <div class="info"><h3>Name Job Tittle here &nbsp;|<small>Oil &amp; Gas Industry Company</small></h3><div class="loc">Location: Place of Middle East here</div>
    <p>Ut ante enim, dapibus malesuada, fringilla eu, condimentum quis, tellus. Aenean porttitor eros vel dolor. venenatis nibh.</p>
    <div class="btns"><span class="btn details">Details</span><span class="btn apply">Apply</span></div></div></article>
  <article class="job" style="top:261px"><div class="thumb" role="img" aria-label="Crew of workers at a refinery"></div>
    <div class="info"><h3>Name Job Tittle here &nbsp;|<small>Oil &amp; Gas Industry Company</small></h3><div class="loc">Location: Place of Middle East here</div>
    <p>Ut ante enim, dapibus malesuada, fringilla eu, condimentum quis, tellus. Aenean porttitor eros vel dolor. venenatis nibh.</p>
    <div class="btns"><span class="btn details">Details</span><span class="btn apply">Apply</span></div></div></article>
  <article class="job" style="top:372px"><div class="thumb" role="img" aria-label="Technician in hard hat inspecting equipment"></div>
    <div class="info"><h3>Name Job Tittle here &nbsp;|<small>Oil &amp; Gas Industry Company</small></h3><div class="loc">Location: Place of Middle East here</div>
    <p>Ut ante enim, dapibus malesuada, fringilla eu, condimentum quis, tellus. Aenean porttitor eros vel dolor. venenatis nibh.</p>
    <div class="btns"><span class="btn details">Details</span><span class="btn apply">Apply</span></div></div></article>
  <div class="view-all" style="position:absolute;left:296px;top:467px">VIEW ALL ▸</div>
</section>

<h2 class="abs sponsors-title">Our Sponsors</h2>
<div class="abs sponsors">
  <span><i></i>Kestrel</span><span>Halden</span><span>Corvane</span><span><i></i>Marlow Bank</span><span>Brightway</span><span>Tessa</span><span>Greenfield Trust</span><span>Solara</span>
</div>

<div class="abs footer-rule"></div>
<nav class="abs footer-nav"><span>About Us</span><span>Jobs</span><span>Services</span><span>Find Now</span><span>Locations</span><span>Support</span><span>Contact</span></nav>
<p class="abs copyright">Copyright 2012 Rigline Careers. All rights reserved. Term of Use</p>
<div class="abs social" aria-label="Social links"><i></i><i></i><i></i><i></i></div>
</body>
</html>
```